Business Card for Coastal Tundrabridge Advisory

We need a business card for Coastal Tundrabridge Advisory. The company website address is provided below. The company logo is attached. We provide specialized permafrost services to the mining, transportation, and oil & gas industries. The card should be prepared for:
Matthias Korhonen, PhD.
Coastal Tundrabridge Advisory
PO Box 418259
Quillwater, Alaska 99642
Direct: +1-907-555-0143
Email: mkorhonen@tundrabridgeadvisory.example
Website: www.coastaltundrabridgeadvisory.example

```html
<!DOCTYPE html>
<html lang="en">
<head>
<meta charset="utf-8">
<title>Coastal Tundrabridge Advisory – Business Card</title>
<link href="https://fonts.googleapis.com/css2?family=Montserrat:wght@400;500;700&display=swap" rel="stylesheet">
<style>
  :root {
    --backdrop: #8c8c8c;
    --navy: #141b29;
    --navy-gloss: #222e45;
    --paper: #ffffff;
    --ink: #111111;
    --ink-soft: #3a3a3a;
  }
  * { margin: 0; padding: 0; box-sizing: border-box; }
  html, body { width: 1200px; height: 900px; overflow: hidden; }
  body {
    background: var(--backdrop);
    font-family: "Montserrat", sans-serif;
    position: relative;
  }
  .card {
    position: absolute;
    width: 560px;
    height: 320px;
    overflow: hidden;
    box-shadow: 0 6px 18px rgba(0,0,0,0.25);
  }
  .card--back {
    left: 100px; top: 110px;
    background: var(--navy);
    display: flex; align-items: center; justify-content: center;
  }
  .back-wordmark {
    color: var(--navy-gloss);
    font-weight: 700;
    font-size: 30px;
    letter-spacing: 2px;
    text-transform: uppercase;
    text-align: center;
    line-height: 1.15;
    width: 380px;
  }
  .card--front {
    left: 540px; top: 470px;
    background: var(--paper);
  }
  .front-shape { position: absolute; inset: 0; }
  .front-wordmark {
    position: absolute;
    left: 28px; top: 100px;
    width: 205px;
    color: var(--ink);
    font-weight: 700;
    font-size: 19px;
    letter-spacing: 1px;
    text-transform: uppercase;
    line-height: 1.15;
  }
  .divider {
    position: absolute;
    left: 248px; top: 44px;
    width: 1px; height: 148px;
    background: var(--ink);
  }
  .details {
    position: absolute;
    left: 260px; top: 38px;
    color: var(--ink-soft);
    font-size: 10.5px;
    line-height: 1.4;
  }
  .details__name { color: var(--ink); font-weight: 700; font-size: 16px; line-height: 1.2; }
  .details__title { margin-bottom: 8px; }
  .details__address { margin-bottom: 8px; }
  .contact { display: flex; align-items: center; gap: 7px; margin-bottom: 3px; }
  .contact svg { width: 10px; height: 10px; flex: none; fill: var(--ink); }
</style>
</head>
<body>

<section class="card card--back" aria-label="Business card back">
  <div class="back-wordmark">Coastal Tundrabridge Advisory</div>
</section>

<section class="card card--front" aria-label="Business card front">
  <svg class="front-shape" viewBox="0 0 560 320" preserveAspectRatio="none" aria-hidden="true">
    <path d="M0 255 Q 330 250 560 205 L560 320 L0 320 Z" fill="var(--navy)"/>
    <path d="M150 244 Q 380 236 545 192 Q 390 244 150 244 Z" fill="var(--ink)"/>
  </svg>

  <div class="front-wordmark">Coastal Tundrabridge Advisory</div>
  <div class="divider"></div>

  <div class="details">
    <div class="details__name">Matthias Korhonen, PhD.</div>
    <div class="details__title">Managing Director</div>
    <div class="details__address">PO Box 418259<br>Quillwater, Alaska 99642</div>
    <div class="contact">
      <svg viewBox="0 0 10 10" aria-hidden="true"><path d="M2 0.5 L3.6 2.4 L2.8 3.6 Q3.8 5.8 6.2 7 L7.4 6.2 L9.5 7.8 L8.4 9.5 Q4 9.4 0.6 5 Q0.2 2.4 2 0.5 Z"/></svg>
      <span>+1-907-555-0143</span>
    </div>
    <div class="contact">
      <svg viewBox="0 0 10 10" aria-hidden="true"><path d="M0.5 2 H9.5 V8.5 H0.5 Z M1 2.5 L5 5.6 L9 2.5" stroke="#fff" stroke-width="0.8"/></svg>
      <span>mkorhonen@tundrabridgeadvisory.example</span>
    </div>
    <div class="contact">
      <svg viewBox="0 0 10 10" aria-hidden="true"><circle cx="5" cy="5" r="4.6"/><path d="M0.5 5 H9.5 M5 0.5 Q2.5 5 5 9.5 M5 0.5 Q7.5 5 5 9.5" stroke="#fff" stroke-width="0.6" fill="none"/></svg>
      <span>www.coastaltundrabridgeadvisory.example</span>
    </div>
  </div>
</section>

</body>
</html>
```